Stylish new business card needed!

Hello everyone! I am in need of a new business card design for an alarm company here in Hurricane WV. I have all fonts, color codes and logos provided for you use! We are a young company and like the style of a clean sleek looking business card. Would like it double sided, one side holding the logo and the other with your design!
Target Market(s)
The people that are looking for the newest tech for home automation and security
Industry/Entity Type
Alarm services; Home automation
Contact Information for Business Card
Name of person; position (Sales; Installer); Phone Number (555.418.7260); Employee cell Number; Website (www.GuardedByVelk.example); Employee Email; Double sided
Look and feel
Each slider illustrates characteristics of the customer's brand and the style your logo design should communicate.

```html
<!DOCTYPE html>
<html lang="en">
<head>
<meta charset="utf-8">
<title>Guarded By Velk – Business Card</title>
<link href="https://fonts.googleapis.com/css2?family=Arimo:wght@400;700&display=swap" rel="stylesheet">
<style>
  :root {
    --backdrop: #232323;
    --card: #222126;
    --card-back: #1d1c20;
    --orange: #f58d4b;
    --grey: #9c9c9c;
    --white: #ffffff;
    --emboss: #121114;
  }
  * { box-sizing: border-box; margin: 0; padding: 0; }
  html, body { width: 1200px; height: 780px; overflow: hidden; }
  body {
    background: var(--backdrop);
    font-family: "Arimo", Arial, sans-serif;
    display: flex;
    align-items: center;
    justify-content: center;
    gap: 40px;
  }
  .card {
    position: relative;
    width: 540px;
    height: 309px;
    border-radius: 16px;
    overflow: hidden;
    background: var(--card);
    box-shadow: 0 0 0 2px var(--orange), 0 14px 30px rgba(0,0,0,.55);
  }
  /* Logo side */
  .card--back { background: var(--card-back); }
  .card--back .brand {
    position: absolute;
    left: 0; right: 0; top: 112px;
    text-align: center;
  }
  .brand__name {
    font-weight: 700;
    font-size: 46px;
    letter-spacing: 1px;
    line-height: 1;
    text-transform: uppercase;
  }
  .card--back .brand__name { color: var(--emboss); }
  .brand__tagline {
    font-weight: 700;
    font-size: 10px;
    letter-spacing: .6px;
    text-transform: uppercase;
    margin-top: 10px;
  }
  .card--back .brand__tagline { color: var(--emboss); }

  /* Info side */
  .card--front .brand {
    position: absolute;
    left: 34px; top: 118px;
    width: 210px;
  }
  .card--front .brand__name { color: var(--orange); font-size: 30px; line-height: 1.05; }
  .card--front .brand__tagline { color: var(--orange); font-size: 7.5px; margin-top: 8px; }
  .divider {
    position: absolute;
    left: 270px; top: 58px;
    width: 2px; height: 150px;
    background: var(--white);
  }
  .contact {
    position: absolute;
    left: 296px; top: 60px;
    color: var(--white);
  }
  .contact__name { font-weight: 700; font-size: 24px; line-height: 1; }
  .contact__first { color: var(--orange); }
  .contact__last { color: var(--grey); }
  .contact__role { font-weight: 700; font-size: 12.5px; margin-top: 4px; }
  .contact__list { list-style: none; margin-top: 18px; }
  .contact__list li {
    display: flex; align-items: center; gap: 8px;
    font-size: 12px; line-height: 17px;
  }
  .contact__list svg { width: 11px; height: 11px; flex: none; }
  .bands { position: absolute; left: 0; bottom: 0; width: 540px; height: 80px; }
</style>
</head>
<body>

  <section class="card card--back" aria-label="Business card, logo side">
    <div class="brand">
      <p class="brand__name">Guarded By Velk</p>
      <p class="brand__tagline">Automation and Security Services</p>
    </div>
  </section>

  <section class="card card--front" aria-label="Business card, contact side">
    <div class="brand">
      <p class="brand__name">Guarded By Velk</p>
      <p class="brand__tagline">Automation and Security Services</p>
    </div>

    <span class="divider"></span>

    <div class="contact">
      <p class="contact__name"><span class="contact__first">Mara</span> <span class="contact__last">Kostelna</span></p>
      <p class="contact__role">Sales; Installer</p>
      <ul class="contact__list">
        <li>
          <svg viewBox="0 0 12 12" aria-hidden="true"><path fill="var(--orange)" d="M2.4 1 4.3 3 3.4 4.4a7 7 0 0 0 4.2 4.2L9 7.7l2 1.9-1.3 1.4C5.6 11 1 6.4 1 2.3z"/></svg>
          555.418.7260
        </li>
        <li>
          <svg viewBox="0 0 12 12" aria-hidden="true"><rect x="3" y="0.8" width="6" height="10.4" rx="1" fill="none" stroke="var(--white)" stroke-width="1.1"/></svg>
          555.302.8841
        </li>
        <li>
          <svg viewBox="0 0 12 12" aria-hidden="true"><circle cx="6" cy="6" r="5" fill="none" stroke="var(--orange)" stroke-width="1.2"/><path d="M1 6h10M6 1c-2.5 3-2.5 7 0 10M6 1c2.5 3 2.5 7 0 10" fill="none" stroke="var(--orange)" stroke-width=".9"/></svg>
          www.GuardedByVelk.example
        </li>
        <li>
          <svg viewBox="0 0 12 12" aria-hidden="true"><rect x="1" y="2.5" width="10" height="7" fill="none" stroke="var(--orange)" stroke-width="1.2"/><path d="M1 2.5 6 6.5l5-4" fill="none" stroke="var(--orange)" stroke-width="1.2"/></svg>
          info@GuardedByVelk.example
        </li>
      </ul>
    </div>

    <svg class="bands" viewBox="0 0 540 80" aria-hidden="true">
      <path fill="var(--grey)" d="M290 42 H540 V22 H318 Z"/>
      <path fill="var(--orange)" d="M0 72 H300 Q318 72 332 54 L338 46 H0 Z"/>
    </svg>
  </section>

</body>
</html>
```